Brochure for Structiva, will be used to hand out to clients.

Need a design for a company brochure (4 pages including front&back + 2 in the middle that looks professional and sells our engineering capabilities to prospective clients. These clients will be architects, builders and developers.

Instructions
1) Open the brochure concept design PDF documents
2) Refer to photo, word files and PDF add in's
3) Setup the Resume section with photo + description and bullet points which can be filled in later (I will advise in 1 or 2 revisions)

The "Services Integration" PDF graph needs a bit of work to tart it up a bit and then inserted into the noted area.

I consider what I have provided as a guideline (neat laid out doc) however you have the ability to change the design if you think it could be better. Must be 4 pages and contain majority of info I have provided.

Target Market(s)

Architects, developers, builders

Industry/Entity Type

Engineering Consultant

Font styles to use
Serif
Sans Serif

Colors
9bcb3b
abd036
cadf82
eaf2ce
86cfc7
cfeae6
fbf289
fee18a
fbc994

Requirements
Must have
• The Brochure should be 4 x A4 pages which is a printed A3 sheet and then folded in half into a neat document.
• Presents well
Nice to have
• Brochure to be professional, minimalistic in a way but also interesting.
• Company colors are in our logo which is predominately green. Will leave colour scheme to the designer

```html
<!DOCTYPE html>
<html lang="en">
<head>
<meta charset="utf-8">
<title>Structiva – Services Spread</title>
<link href="https://fonts.googleapis.com/css2?family=Michroma&family=Exo+2:ital,wght@0,400;0,600;0,700;1,600;1,700&display=swap" rel="stylesheet">
<style>
  :root{
    --backdrop:#2e2e2e;
    --paper:#ffffff;
    --paper-shade:#f1f2f0;
    --green-light:#cadf82;
    --green-mid:#9bcb3b;
    --green-leaf:#abd036;
    --green-deep:#4f9a2c;
    --green-dark:#3a8527;
    --green-pale:#eaf2ce;
    --ink:#333333;
    --ink-soft:#5b5b5b;
    --rule:#dcdedb;
  }
  *{box-sizing:border-box;margin:0;padding:0}
  html,body{width:1200px;height:833px;overflow:hidden;background:var(--backdrop)}
  body{font-family:"Exo 2",sans-serif;color:var(--ink)}
  .spread{position:absolute;left:60px;top:34px;width:1080px;height:764px;display:flex;box-shadow:0 10px 30px rgba(0,0,0,.45)}
  .page{position:relative;width:540px;height:764px;background:var(--paper);overflow:hidden}
  .page--left{background:linear-gradient(90deg,#fff 85%,#ececec 100%)}
  .page--right{background:linear-gradient(90deg,#e9e9e9 0%,#fff 12%)}
  .page-band{position:absolute;left:0;top:0;width:540px;height:140px}
  .page-title{position:absolute;top:30px;font-family:"Michroma",sans-serif;color:#fff;font-size:17px;letter-spacing:8px;font-style:italic}
  .page--left .page-title{left:64px}
  .page--right .page-title{left:50px;top:34px;font-size:16px;letter-spacing:9px}

  /* services */
  .service{position:absolute;left:36px;width:470px;height:118px}
  .service-card{position:absolute;left:0;top:12px;width:470px;height:106px;border:1px solid var(--rule);border-radius:10px;background:linear-gradient(90deg,var(--paper-shade),#fff 70%)}
  .service-tab{position:absolute;left:22px;top:0;width:150px;height:22px;background:linear-gradient(90deg,var(--green-deep),var(--green-mid));color:#fff;font-style:italic;font-weight:700;font-size:10px;letter-spacing:.5px;line-height:22px;padding-left:20px;text-transform:uppercase}
  .service-body{position:absolute;left:14px;top:28px;width:322px;font-size:6.6px;line-height:1.25;color:var(--ink-soft)}
  .service-body h4{font-size:7.2px;font-weight:700;color:var(--ink);margin:3px 0 1px}
  .expertise{list-style:none;display:grid;grid-template-columns:186px 128px;column-gap:8px}
  .expertise li{white-space:nowrap}
  .expertise li::before{content:"✓ ";color:var(--green-deep)}
  .service-media{position:absolute;right:10px;top:22px;width:120px;height:86px;border-radius:6px}

  /* right page */
  .intro{position:absolute;left:50px;top:112px;width:450px;font-size:8.4px;line-height:1.35;color:var(--ink-soft)}
  .intro p{margin-bottom:5px}
  .flow-chart{position:absolute;left:40px;top:188px;width:470px;height:250px}
  .section-heading{position:absolute;left:50px;font-style:italic;font-weight:700;font-size:14px;color:var(--green-deep);text-transform:uppercase;letter-spacing:.3px}
  .section-text{position:absolute;left:50px;width:450px;font-size:8.4px;line-height:1.35;color:var(--ink-soft)}
  .bim-shot{position:absolute;top:528px;height:112px;border-radius:4px}
</style>
</head>
<body>
<div class="spread">

  <section class="page page--left">
    <svg class="page-band" viewBox="0 0 540 140" aria-hidden="true">
      <defs><linearGradient id="bandL" x1="0" x2="1"><stop offset="0" stop-color="#9bcb3b"/><stop offset="1" stop-color="#abd036"/></linearGradient></defs>
      <path d="M0 0H540V58Q300 70 150 84Q60 92 0 96Z" fill="url(#bandL)"/>
    </svg>
    <h2 class="page-title">OUR SERVICES</h2>

    <article class="service" style="top:100px">
      <div class="service-card"></div>
      <div class="service-tab">Mechanical</div>
      <div class="service-body">
        <p>Through a collaborative effort involving architects and our in-house Mechanical Engineers Structiva deliver innovative sustainable design solutions that are robust, coordinated, efficient and provide a high-quality indoor environment.</p>
        <h4>Areas of Expertise</h4>
        <ul class="expertise"><li>Fully Coordinated Designs with Building Services</li><li>Plantrooms</li><li>Energy Efficiency</li><li>Cogeneration and Trigeneration</li><li>Under Floor and Displacement Air Conditioning</li><li>Active/ Passive Chilled Beams</li></ul>
      </div>
      <div class="service-media" role="img" aria-label="Mechanical plant schematic drawing" style="background:linear-gradient(135deg,#f4f4f4,#d9dcd8)"></div>
    </article>

    <article class="service" style="top:228px">
      <div class="service-card"></div>
      <div class="service-tab">Electrical</div>
      <div class="service-body">
        <p>Structiva's Electrical Engineering Services team is a leading provider of lighting and power system design solutions to the Australian market.</p>
        <h4>Areas of Expertise</h4>
        <ul class="expertise"><li>Electrical supply infrastructure</li><li>Central and Distributed Power Systems</li><li>Standby Power Supplies</li><li>Electrical Distribution systems</li><li>Lighting Design</li><li>Exit and Emergency Lighting</li><li>Lightning and Surge Protection</li><li>Intrinsically safe installations</li></ul>
      </div>
      <div class="service-media" role="img" aria-label="Electrical tools on wiring plans" style="background:linear-gradient(135deg,#e6ebee,#c9d1d6 60%,#e58a4a)"></div>
    </article>

    <article class="service" style="top:356px">
      <div class="service-card"></div>
      <div class="service-tab">Hydraulic</div>
      <div class="service-body">
        <p>Structiva has the ability to provide Hydraulic designs for Cold and Hot Water supplies, Sewer Drainage and Water Management strategies that include water harvesting, treatment and recycling of grey and black water for toilet flushing and/or landscape irrigation.</p>
        <h4>Areas of Expertise</h4>
        <ul class="expertise"><li>Liaison with Service Authorities</li><li>Site Infrastructure</li><li>Property Sewer Drainage</li><li>Sanitary Plumbing Installations</li><li>Trade Waste Drainage and Treatment Apparatus</li><li>Domestic Heated Water Services</li></ul>
      </div>
      <div class="service-media" role="img" aria-label="Copper pipe fittings on hydraulic plans" style="background:linear-gradient(135deg,#eeeeee,#d4d4d4 55%,#d08a55)"></div>
    </article>

    <article class="service" style="top:484px">
      <div class="service-card"></div>
      <div class="service-tab">Fire</div>
      <div class="service-body">
        <p>Structiva provides Fire Services engineering which encompasses the design of conventional Fire Suppression and Detection systems, including sprinklers, fire alarm systems, fire hydrants and hose reels and multi point aspirating smoke detection systems for highly sensitive and critical equipment rooms.</p>
        <h4>Areas of Expertise</h4>
        <ul class="expertise"><li>Fully Coordinated Designs with Building Services</li><li>Plantrooms</li><li>Energy Efficiency</li><li>Cogeneration and Trigeneration</li><li>Under Floor and Displacement Air Conditioning</li><li>Active/ Passive Chilled Beams</li></ul>
      </div>
      <div class="service-media" role="img" aria-label="Fire sprinkler heads on a bench" style="background:linear-gradient(135deg,#eeeeee,#dadada 60%,#d9603a)"></div>
    </article>

    <article class="service" style="top:612px">
      <div class="service-card"></div>
      <div class="service-tab">Sustainability</div>
      <div class="service-body">
        <p>Through a collaborative effort involving architects and our in-house Mechanical Engineers Structiva deliver innovative sustainable design solutions that are robust, coordinated, efficient and provide a high-quality indoor environment.</p>
        <h4>Areas of Expertise</h4>
        <ul class="expertise"><li>Fully Coordinated Designs with Building Services</li><li>Plantrooms</li><li>Energy Efficiency</li><li>Cogeneration and Trigeneration</li><li>Under Floor and Displacement Air Conditioning</li><li>Active/ Passive Chilled Beams</li></ul>
      </div>
      <div class="service-media" role="img" aria-label="Sustainable house ventilation diagram" style="background:linear-gradient(135deg,#fafafa,#e2e4e2)"></div>
    </article>
  </section>

  <section class="page page--right">
    <svg class="page-band" viewBox="0 0 540 140" aria-hidden="true">
      <defs><linearGradient id="bandR" x1="0" x2="1"><stop offset="0" stop-color="#abd036"/><stop offset="1" stop-color="#6fae32"/></linearGradient></defs>
      <path d="M0 0H540V118Q420 98 260 94Q110 92 0 92Z" fill="url(#bandR)"/>
    </svg>
    <h2 class="page-title">SERVICES INTEGRATION</h2>

    <div class="intro">
      <p>Structiva provide services integration as demonstrated below to ensure our designs are coordinated, compliant and correct.</p>
      <p>If required, we can work with our clients and contractors to undertake peer reviews of designs. We can assist in value engineering to ensure the most effective design whilst remaining compliant with the design brief.</p>
      <p>We work with contractors during the tendering phase to enable them to achieve targeted pricing.</p>
    </div>

    <svg class="flow-chart" viewBox="0 0 470 250" role="img" aria-label="Four-stage services integration chart">
      <defs>
        <linearGradient id="col" x1="0" x2="1"><stop offset="0" stop-color="#3f9a2e"/><stop offset=".55" stop-color="#8cc35a"/><stop offset="1" stop-color="#5aa634"/></linearGradient>
        <linearGradient id="head" x1="0" x2="1"><stop offset="0" stop-color="#4f9a2c"/><stop offset="1" stop-color="#9bcb3b"/></linearGradient>
      </defs>
      <rect x="0" y="0" width="470" height="250" fill="url(#col)"/>
      <g fill="url(#head)">
        <rect x="0" y="0" width="117" height="20"/>
        <rect x="117" y="12" width="117" height="20"/>
        <rect x="234" y="24" width="118" height="20"/>
        <rect x="352" y="36" width="118" height="20"/>
      </g>
      <g stroke="#cadf82" stroke-width="1.5" fill="none">
        <path d="M117 20V90l6 6-6 6V250"/>
        <path d="M234 32V110l6 6-6 6V250"/>
        <path d="M352 44V130l6 6-6 6V250"/>
        <path d="M0 20H117M117 32H234M234 44H352M352 56H470" stroke-width="1"/>
      </g>
      <g fill="#fff" font-family="Michroma, sans-serif" font-size="7.5">
        <text x="18" y="13.5">LOREM IPSUM</text>
        <text x="135" y="25.5">LOREM IPSUM</text>
        <text x="252" y="37.5">LOREM IPSUM</text>
        <text x="370" y="49.5">LOREM IPSUM</text>
      </g>
    </svg>

    <h3 class="section-heading" style="top:458px">Modelra BIM Modeling</h3>
    <p class="section-text" style="top:478px">Our in-house drafting team are qualified and trusted with the ability to produce designs in DraftCore or 3D Modelra. Some examples of our coordinated drafting works are indicated below.</p>

    <div class="bim-shot" role="img" aria-label="Rendered 3D pipework in a plant room" style="left:40px;width:150px;background:linear-gradient(135deg,#5a6066,#2f3336 60%,#8a9096)"></div>
    <div class="bim-shot" role="img" aria-label="3D model software view with ductwork" style="left:198px;width:150px;background:linear-gradient(135deg,#dfe6ee,#3a3c3e 45%,#e24a4a 75%,#2e2e2e)"></div>
    <div class="bim-shot" role="img" aria-label="Coordination schedule spreadsheet" style="left:356px;width:144px;background:linear-gradient(90deg,#f3f6fb,#c9dcef 45%,#f2e37a 70%,#f3f6fb)"></div>

    <h3 class="section-heading" style="top:656px">Value Engineering</h3>
    <div class="section-text" style="top:676px">
      <p style="margin-bottom:6px">Structiva specialise in working with our clients and contractors to undertake peer reviews of designs. We can assist in value engineering to ensure the most effective design whilst remaining compliant with the design brief.</p>
      <p>We work with contractors during the tendering phase to enable them to achieve targeted pricing.</p>
    </div>
  </section>

</div>
</body>
</html>
```